Stationary Suite for Aussie Law Firm

We are a small law firm operating out of Albany, Western Australia. We have a logo, which we love and was the winner of a ArtworkHive contest last year.
We require a suite of business stationary products incorporating our logo and contact details. These should be:
1. Letterhead (A4)
The letterhead should incorporate the following information in addition to the logo:
ABN 38 602 917 255 (this is our Australian Business Number)
Beatrix Lund atf The BJL Legal Trust t/as Harbour Gate Legal & Conveyancing (legal name of the business)
Address: Wexley House, Wexley Street, Albany
Postal Address: PO Box 8147, Albany WA 6332
Telephone: 0491 670 382
Facsimile: 08 9722 5913
Email: info@harbourgatelegal.com.au
Website: www.harbourgatelegal.com.au
2. Business Card (90mm x 55mm)
I've attached my current business card layout just for your information.
The front of the business card should include the following information in addition to the logo:
Beatrix Lund
Director & Principal Solicitor
Telephone: 0491 670 382
Facsimile: 08 9722 5913
Email: beatrix@harbourgatelegal.com.au
The back of the card should be similar to the back of my existing card, but should only have the logo in white and the address of our website (www.harbourgatelegal.com.au)
3. Email signature block
This should include the same information as the front of the business card.
4. With Compliments slip (DL size)
The With Compliments slip should include the same information as the Letterhead.
5. Banner (830mm x 2000mm)
We need a banner designed for use at marketing events. This should include our website details and logo - other than that you have fairly free reign with the design.
6. Flyer (DL)
We need a flyer setting out our services and main contact details for use at marketing events. The details to be included are:
Telephone: 0491 670 382
Web: www.harbourgatelegal.com.au
Areas of law:
Wills & Estate Planning
Probate & Letters of Administration
Property Law & Conveyancing
General Commercial Law
Business Law
Style guide:
Please look at our website for an idea as to the style of designs we are looking for - www.harbourgatelegal.com.au. The design should be modern, sharp and professional.
Colours:
The CMYK details for the colours in our logo are:
Light Blue C72 M5 Y0 K0
Dark Blue C97 M72 Y16 K30
Edit 31/7/2014
I have added a couple of photos that we have used on our website, and additional photos. These are from our local area, so feel free to use these in your designs or to inform them.
- Calibri, Century Gothic

```html
<!DOCTYPE html>
<html lang="en">
<head>
<meta charset="utf-8">
<title>Harbour Gate Legal &amp; Conveyancing — Flyer Set</title>
<link rel="stylesheet" href="https://fonts.googleapis.com/css2?family=Roboto+Condensed:wght@400;700&display=swap">
<style>
  :root {
    --dark-blue: #0d3f6e;
    --light-blue: #2aa8e0;
    --white: #ffffff;
    --stage: #4a3223;
    --sky-top: #1d4f80;
    --sky-low: #b9cde0;
  }
  * { margin: 0; padding: 0; box-sizing: border-box; }
  html, body { width: 1200px; height: 1000px; overflow: hidden; }
  body {
    background: var(--stage);
    font-family: "Roboto Condensed", Arial, sans-serif;
    position: relative;
  }
  .flyer { position: absolute; overflow: hidden; background: var(--white); }

  /* Landscape flyer, banded */
  .flyer-banded { left: 43px; top: 135px; width: 730px; height: 350px; }
  .flyer-banded .wave-wash {
    position: absolute; inset: 0 0 67px 0;
    background: linear-gradient(160deg, #ffffff 0%, #e3f0fa 35%, #ffffff 60%);
  }
  .flyer-banded .gavel-photo {
    position: absolute; left: 290px; top: 40px; width: 440px; height: 243px;
    background: linear-gradient(180deg, #f4f4f4 0%, #9a9a9a 55%, #d8d8d8 100%);
  }
  .flyer-banded .services {
    position: absolute; left: 0; top: 62px; width: 415px;
    text-align: center; list-style: none;
    color: var(--light-blue); font-weight: 700; font-size: 25px; line-height: 32.5px;
  }
  .flyer-banded .brand { position: absolute; right: 22px; top: 70px; }
  .flyer-banded .contact-band {
    position: absolute; left: 0; right: 0; bottom: 0; height: 67px;
    background: var(--dark-blue); color: var(--white);
  }
  .flyer-banded .contact-line { position: absolute; left: 42px; top: 27px; font-size: 12px; }
  .flyer-banded .web { position: absolute; right: 48px; top: 18px; font-size: 22px; font-weight: 700; }

  .label { color: var(--light-blue); }

  /* Landscape flyer, split */
  .flyer-split { left: 43px; top: 505px; width: 730px; height: 350px; }
  .flyer-split .side-panel {
    position: absolute; left: 0; top: 0; width: 309px; height: 100%;
    background: var(--dark-blue); color: var(--white); text-align: center;
  }
  .flyer-split .brand { position: absolute; left: 0; right: 0; top: 125px; }
  .flyer-split .web { position: absolute; left: 0; right: 0; top: 220px; font-size: 20px; font-weight: 700; }
  .flyer-split .contact { position: absolute; left: 0; right: 0; top: 249px; font-size: 12.5px; line-height: 16px; }
  .flyer-split .services {
    position: absolute; right: 48px; top: 50px; text-align: right; list-style: none;
    color: var(--light-blue); font-size: 26px; line-height: 30.5px;
  }
  .flyer-split .gavel-photo {
    position: absolute; left: 437px; top: 200px; width: 293px; height: 150px;
    background: linear-gradient(180deg, #ffffff 0%, #b0b0b0 50%, #e6e6e6 100%);
  }

  /* Portrait flyer */
  .flyer-tall {
    left: 802px; top: 135px; width: 354px; height: 735px;
    background: linear-gradient(180deg, var(--dark-blue) 0%, var(--sky-top) 40%, var(--sky-low) 62%, #dfe7ef 100%);
    color: var(--white); text-align: center;
  }
  .flyer-tall .brand { position: absolute; left: 0; right: 0; top: 135px; }
  .flyer-tall .services {
    position: absolute; left: 0; right: 0; top: 211px; list-style: none;
    font-size: 18px; line-height: 21.5px;
  }
  .flyer-tall .statue-photo {
    position: absolute; left: 10px; top: 330px; width: 334px; height: 405px;
    background: linear-gradient(180deg, #c9a98c 0%, #a88569 60%, #8c6b52 100%);
    border-radius: 120px 120px 0 0;
  }
  .flyer-tall .contact-band {
    position: absolute; left: 0; right: 0; top: 643px; height: 72px;
    background: rgba(13, 63, 110, 0.88);
  }
  .flyer-tall .web { margin-top: 10px; font-size: 20px; font-weight: 700; }
  .flyer-tall .contact { font-size: 12.5px; line-height: 16px; }

  /* Brand name set in text */
  .brand-name {
    font-weight: 400; text-transform: uppercase; letter-spacing: 1px; line-height: 1.15;
  }
  .flyer-banded .brand-name { color: var(--dark-blue); font-size: 15px; text-align: center; }
  .flyer-split .brand-name, .flyer-tall .brand-name { color: var(--white); font-size: 21px; }

  .caption {
    position: absolute; left: 0; width: 1260px; top: 888px; text-align: center;
    color: var(--white); font-family: Arial, Helvetica, sans-serif; font-size: 64px;
  }
</style>
</head>
<body>

<section class="flyer flyer-banded">
  <div class="wave-wash"></div>
  <div class="gavel-photo" role="img" aria-label="Photo of a wooden gavel resting on an open law book"></div>
  <ul class="services">
    <li>Wills &amp; Estate Planning</li>
    <li>Probate &amp; Letters of Administration</li>
    <li>Property Law &amp; Conveyancing</li>
    <li>General Commercial Law</li>
    <li>Business Law</li>
  </ul>
  <div class="brand"><p class="brand-name">Harbour Gate<br>Legal &amp; Conveyancing</p></div>
  <div class="contact-band">
    <p class="contact-line"><span class="label">Telephone</span> 0491 670 382 &nbsp; <span class="label">Email</span> info@harbourgatelegal.com.au</p>
    <p class="web">www.harbourgatelegal.com.au</p>
  </div>
</section>

<section class="flyer flyer-split">
  <div class="side-panel">
    <div class="brand"><p class="brand-name">Harbour Gate<br>Legal &amp; Conveyancing</p></div>
    <p class="web">www.harbourgatelegal.com.au</p>
    <p class="contact"><span class="label">Telephone</span> 0491 670 382<br><span class="label">Email</span> info@harbourgatelegal.com.au</p>
  </div>
  <ul class="services">
    <li>Wills &amp; Estate Planning</li>
    <li>Probate &amp; Letters of Administration</li>
    <li>Property Law &amp; Conveyancing</li>
    <li>General Commercial Law</li>
    <li>Business Law</li>
  </ul>
  <div class="gavel-photo" role="img" aria-label="Photo of a wooden gavel on an open book"></div>
</section>

<section class="flyer flyer-tall">
  <div class="statue-photo" role="img" aria-label="Photo of a stone statue of Justice holding scales against the sky"></div>
  <div class="brand"><p class="brand-name">Harbour Gate<br>Legal &amp; Conveyancing</p></div>
  <ul class="services">
    <li>Wills &amp; Estate Planning</li>
    <li>Probate &amp; Letters of Administration</li>
    <li>Property Law &amp; Conveyancing</li>
    <li>General Commercial Law</li>
    <li>Business Law</li>
  </ul>
  <div class="contact-band">
    <p class="web">www.harbourgatelegal.com.au</p>
    <p class="contact"><span class="label">Telephone</span> 0491 670 382<br><span class="label">Email</span> info@harbourgatelegal.com.au</p>
  </div>
</section>

<p class="caption">Flyer</p>

</body>
</html>
```